Business Card Design

New business card design

Target Market(s)

Residential & Commercial Property Managers

Industry/Entity Type

Plumbing Services

Contact Information for Business Card

Name - Rowan Keddle, title - Director, Phone Number - 0431 286 517, email - rowan@tbk-plumbing.com.au, Company ABN - 73 215 904 386,

Font styles to use
Sans Serif

Colors
0054AA
0677BA
7BADD7
CADEEF
E8F1F8

```html
<!DOCTYPE html>
<html lang="en">
<head>
<meta charset="utf-8">
<title>TBK Plumbing Services – Business Card</title>
<link rel="stylesheet" href="https://fonts.googleapis.com/css2?family=Poppins:wght@300;400;600&display=swap">
<style>
  :root {
    --stage: #222222;
    --card: #1b222b;
    --card-edge: #151b22;
    --band: rgba(0, 0, 0, 0.28);
    --white: #ffffff;
    --blue: #29a3e0;
    --blue-deep: #0677ba;
    --taupe: #8a7f72;
    --muted: #d9dde2;
  }
  * { margin: 0; padding: 0; box-sizing: border-box; }
  html, body {
    width: 1200px; height: 780px; overflow: hidden;
    background: var(--stage);
    font-family: "Poppins", Arial, sans-serif;
  }
  .stage {
    width: 1200px; height: 780px;
    display: flex; align-items: center; justify-content: center; gap: 40px;
  }
  .card {
    position: relative;
    width: 540px; height: 309px;
    background: var(--card);
    border-radius: 3px;
    box-shadow: 0 0 0 1px var(--card-edge), 0 14px 30px rgba(0,0,0,0.45);
    overflow: hidden;
  }

  /* brand lockup */
  .brand { display: flex; align-items: center; gap: 12px; }
  .brand-dot { width: 14px; height: 14px; border-radius: 50%; background: var(--blue); flex: none; }
  .brand-name { color: var(--white); font-weight: 300; white-space: nowrap; }

  /* back of card */
  .card-back { display: flex; align-items: center; justify-content: center; }
  .card-back .brand-name { font-size: 34px; letter-spacing: 1px; }
  .card-back .brand-dot { width: 20px; height: 20px; }

  /* front of card */
  .card-front .shade {
    position: absolute; left: -40px; top: 110px; width: 640px; height: 90px;
    background: linear-gradient(180deg, transparent, var(--band) 50%, transparent);
    transform: rotate(-8deg);
  }
  .card-front .brand { position: absolute; top: 38px; right: 38px; }
  .card-front .brand-name { font-size: 20px; }
  .details { position: absolute; left: 44px; top: 92px; }
  .person { font-size: 30px; line-height: 1.1; }
  .person-first { color: var(--blue); font-weight: 600; }
  .person-last { color: var(--taupe); font-weight: 300; }
  .role { color: var(--white); font-size: 13px; margin-top: 4px; }
  .abn { color: var(--blue); font-size: 13px; font-weight: 300; margin-top: 6px; letter-spacing: 0.3px; }
  .contacts { list-style: none; margin-top: 18px; display: grid; gap: 8px; }
  .contact { display: flex; align-items: center; gap: 10px; color: var(--muted); font-size: 12.5px; font-weight: 300; }
  .contact-icon { width: 18px; height: 18px; flex: none; }
</style>
</head>
<body>
<main class="stage">

  <section class="card card-front" aria-label="Business card front">
    <div class="shade"></div>
    <div class="brand">
      <span class="brand-dot"></span>
      <span class="brand-name">TBK Plumbing Services</span>
    </div>
    <div class="details">
      <h1 class="person"><span class="person-first">Rowan</span> <span class="person-last">Keddle</span></h1>
      <p class="role">Director</p>
      <p class="abn">ABN - 73 215 904 386</p>
      <ul class="contacts">
        <li class="contact">
          <svg class="contact-icon" viewBox="0 0 18 18" aria-hidden="true">
            <rect x="3" y="3" width="12" height="12" rx="2" transform="rotate(45 9 9)" fill="var(--blue)"/>
            <path d="M6.6 5.8l1.3-.3.7 1.7-.8.6a5 5 0 0 0 2.4 2.4l.6-.8 1.7.7-.3 1.3c-3 .3-5.9-2.6-5.6-5.6z" fill="var(--white)"/>
          </svg>
          0431 286 517
        </li>
        <li class="contact">
          <svg class="contact-icon" viewBox="0 0 18 18" aria-hidden="true">
            <rect x="3" y="3" width="12" height="12" rx="2" transform="rotate(45 9 9)" fill="var(--blue)"/>
            <rect x="5.5" y="6.5" width="7" height="5" rx="0.6" fill="var(--white)"/>
            <path d="M5.7 6.8L9 9.3l3.3-2.5" stroke="var(--blue)" stroke-width="0.8" fill="none"/>
          </svg>
          rowan@tbk-plumbing.com.au
        </li>
        <li class="contact">
          <svg class="contact-icon" viewBox="0 0 18 18" aria-hidden="true">
            <rect x="3" y="3" width="12" height="12" rx="2" transform="rotate(45 9 9)" fill="var(--blue)"/>
            <circle cx="9" cy="9" r="3.6" fill="none" stroke="var(--white)" stroke-width="0.9"/>
            <ellipse cx="9" cy="9" rx="1.5" ry="3.6" fill="none" stroke="var(--white)" stroke-width="0.8"/>
            <path d="M5.4 9h7.2" stroke="var(--white)" stroke-width="0.8"/>
          </svg>
          www.tbk-plumbing.com.au
        </li>
      </ul>
    </div>
  </section>

  <section class="card card-back" aria-label="Business card back">
    <div class="brand">
      <span class="brand-dot"></span>
      <span class="brand-name">TBK Plumbing Services</span>
    </div>
  </section>

</main>
</body>
</html>
```